Larkspur Energy - Stock Certificate

We need a custom designed stock certificate that represents the look of our company logo but also have a cool look compared to a standard stock certificate. We thinking we want the logo in gold. Our website is https://www.larkspurenergyusa.example.

We are wanting the certificate to look very professional and really cool, we have sales agents that work for the company and we are creating a program by which the sales agents can gain ownership in the company. So the certificates need to have a very cool appeal and that provides a sense of pride in owning "Units" in Larkspur Energy.

Reason: Extending so other board members can vote as well, thank you all!

Target Market(s)

Stock/Shareholders

Industry/Entity Type

It Company

Font styles to use
Script

Requirements
Must have
• Must look like a stock certificate, must use our logo which the psd file for it was attached.
Nice to have
• Nice to have the logo in gold

```html
<!DOCTYPE html>
<html lang="en">
<head>
<meta charset="utf-8">
<title>Larkspur Energy – Stock Certificate</title>
<link rel="stylesheet" href="https://fonts.googleapis.com/css2?family=Arimo:wght@400&family=Great+Vibes&family=Open+Sans:ital@1&family=UnifrakturMaguntia&display=swap">
<style>
  :root {
    --ink: #000000;
    --map: #2b2b2b;
    --map-light: #353535;
    --paper-text: #ffffff;
    --frame-orange: #e8590c;
    --frame-amber: #f59a16;
    --frame-gold: #ffd43a;
    --seal: #f08a1c;
  }
  html, body {
    margin: 0;
    padding: 0;
    overflow: hidden;
    background: var(--ink);
  }
  .certificate {
    position: relative;
    width: 1200px;
    height: 848px;
    overflow: hidden;
    background: var(--ink);
    color: var(--paper-text);
    font-family: "Arimo", Arial, sans-serif;
  }
  .certificate__art {
    position: absolute;
    inset: 0;
  }
  .title {
    position: absolute;
    left: 0;
    right: 0;
    top: 82px;
    margin: 0;
    text-align: center;
    font-family: "UnifrakturMaguntia", serif;
    font-weight: 400;
    font-size: 90px;
    line-height: 1;
    letter-spacing: 1px;
  }
  .brand {
    position: absolute;
    left: 88px;
    top: 250px;
    width: 276px;
    text-align: center;
  }
  .brand__mark {
    width: 150px;
    height: 150px;
    margin: 0 auto 150px;
    border-radius: 50%;
    background: var(--seal);
  }
  .brand__name {
    font-family: "Arimo", Arial, sans-serif;
    font-weight: 400;
    font-size: 31px;
    color: var(--paper-text);
    letter-spacing: 1px;
    white-space: nowrap;
  }
  .line {
    position: absolute;
    margin: 0;
    font-size: 19.5px;
    line-height: 1.3;
    white-space: nowrap;
  }
  .line--center {
    left: 352px;
    width: 800px;
    text-align: center;
  }
  .certifies { top: 250px; }
  .holder {
    position: absolute;
    left: 516px;
    top: 312px;
    width: 476px;
    height: 88px;
    border-bottom: 1.5px solid var(--paper-text);
    text-align: center;
    font-family: "Great Vibes", cursive;
    font-size: 86px;
    line-height: 1;
    padding-left: 20px;
    box-sizing: border-box;
  }
  .entitled { left: 402px; top: 430px; }
  .stock-class { left: 478px; top: 455px; }
  .blank {
    position: relative;
    display: inline-block;
    border-bottom: 1.5px solid var(--paper-text);
    height: 17px;
    vertical-align: baseline;
    text-align: center;
  }
  .blank__value {
    position: absolute;
    left: 0;
    right: 0;
    bottom: 0;
    font-family: "Great Vibes", cursive;
    font-size: 28px;
    line-height: 1;
  }
  .blank__value--small { font-size: 24px; bottom: -4px; }
  .blank--shares { width: 44px; margin: 0 4px; }
  .blank--par { width: 166px; margin: 0 2px 0 6px; }
  .blank--class { width: 236px; margin-right: 14px; }
  .transfer { top: 505px; }
  .witness { top: 583px; }
  .signatures {
    position: absolute;
    top: 710px;
    left: 534px;
    display: flex;
    gap: 135px;
  }
  .signature {
    width: 143px;
    border-top: 1.5px solid var(--paper-text);
    padding-top: 2px;
    text-align: center;
    font-family: "Open Sans", Arial, sans-serif;
    font-style: italic;
    font-size: 21px;
  }
</style>
</head>
<body>
<main class="certificate">
  <svg class="certificate__art" width="1200" height="848" viewBox="0 0 1200 848" aria-hidden="false">
    <defs>
      <linearGradient id="frameGradient" x1="0" y1="0" x2="0.15" y2="1">
        <stop offset="0" stop-color="var(--frame-orange)"/>
        <stop offset="0.35" stop-color="var(--frame-amber)"/>
        <stop offset="0.65" stop-color="var(--frame-gold)"/>
        <stop offset="0.9" stop-color="var(--frame-amber)"/>
        <stop offset="1" stop-color="var(--frame-orange)"/>
      </linearGradient>
      <radialGradient id="mapTone" cx="0.55" cy="0.45" r="0.7">
        <stop offset="0" stop-color="var(--map-light)"/>
        <stop offset="1" stop-color="var(--map)"/>
      </radialGradient>
    </defs>
    <rect class="map-backdrop" x="0" y="0" width="1200" height="848" fill="url(#mapTone)" opacity="0.55" role="img" aria-label="Faint grey world map spanning the certificate background"/>
    <path class="frame" fill="none" stroke="url(#frameGradient)" stroke-width="6"
      d="M76 19 H1126 A56 56 0 0 0 1182 75 V773 A56 56 0 0 0 1126 829 H76 A56 56 0 0 0 20 773 V75 A56 56 0 0 0 76 19 Z"/>
  </svg>

  <h1 class="title">Stock Certificate</h1>

  <div class="brand">
    <div class="brand__mark"></div>
    <div class="brand__name">Larkspur Energy</div>
  </div>

  <p class="line line--center certifies">This certifies that</p>
  <div class="holder">John Doe</div>

  <p class="line entitled">is entitled to<span class="blank blank--shares"><span class="blank__value">55</span></span>shares of the par value of<span class="blank blank--par"><span class="blank__value">120$</span></span>each of the</p>
  <p class="line stock-class"><span class="blank blank--class"><span class="blank__value blank__value--small">Common stock</span></span>of the Larkspur Energy Company</p>

  <p class="line line--center transfer">transferable in person or by Attorney only in the books of the Company and upon<br>the surrender of this Certificate.</p>
  <p class="line line--center witness">In witness whereof the Larkspur Energy Company has caused this Certificate to be</p>

  <div class="signatures">
    <div class="signature">Signature</div>
    <div class="signature">Signature</div>
  </div>
</main>
</body>
</html>
```